Mobile Fitness snd Therapy Business Card Design

I need a business card designed for my mobile fitness and therapy business.

Please view the images that I have uploaded. I like the simplicity of the design that I have attached. I adapted it with my information

Target Market(s)

Those seeking personal training, injury rehabilitation or massage therapy.

Industry/Entity Type

Business

Contact Information for Business Card

Derek Fulham - MSc, CAT(C), RMT, CSCS, Pn2
e-mail: derek@vantrelo.com
website: www.vantrelo.com
instagram: @derek_fulham

Font styles to use
Sans Serif

Colors
3176b5
0355a3

Requirements
Must have
• "Contact us to receive a FREE assessment"
• Services offered:
• Personal Training
• Golf Fitness
• Injury Rehab
• Massage Therapy
• Yoga
Nice to have
• Consistent colours with brand
• - Dark Blue: #232837
• - Blue: #5096f0
• Consistent look/feel with the website: www.vantrelo.com

```html
<!DOCTYPE html>
<html lang="en">
<head>
<meta charset="utf-8">
<title>Vantrelo Business Card</title>
<link href="https://fonts.googleapis.com/css2?family=Roboto:wght@400;500;700;900&display=swap" rel="stylesheet">
<style>
  :root {
    --stage: #e6e6e8;
    --navy: #2b3040;
    --navy-deep: #232837;
    --blue: #3d8fe0;
    --blue-strong: #0355a3;
    --ink: #1f2533;
    --paper: #ffffff;
    --muted: #c9ccd2;
  }
  * { box-sizing: border-box; margin: 0; padding: 0; }
  html, body {
    width: 1200px; height: 852px; overflow: hidden;
    background: var(--stage);
    font-family: "Roboto", Arial, sans-serif;
  }
  .stage {
    position: relative; width: 1200px; height: 852px;
    display: flex; align-items: center; justify-content: center; gap: 50px;
  }
  .card {
    position: relative; width: 525px; height: 300px;
    border-radius: 22px; overflow: hidden;
    box-shadow: 0 6px 18px rgba(0,0,0,.18);
  }

  /* Back of card */
  .card-back {
    background: linear-gradient(160deg, #363b4b 0%, var(--navy-deep) 100%);
    color: #e9ecf2;
  }
  .back-brand {
    position: absolute; top: 92px; left: 0; right: 0;
    display: flex; align-items: center; justify-content: center; gap: 14px;
  }
  .back-brand .dot {
    width: 22px; height: 22px; border-radius: 50%; background: var(--blue);
  }
  .back-brand .name {
    font-weight: 900; font-size: 44px; letter-spacing: 3px; color: var(--blue);
  }
  .services {
    position: absolute; bottom: 34px; left: 0; right: 0;
    text-align: center; font-size: 14px; line-height: 20px; color: #e4e7ee;
  }
  .services .sep {
    display: inline-block; width: 2px; height: 11px; margin: 0 7px;
    background: var(--blue); vertical-align: -1px;
  }

  /* Front of card */
  .card-front { background: var(--paper); color: var(--ink); }
  .edge-tab {
    position: absolute; width: 14px; height: 120px; border-radius: 8px;
    background: var(--navy-deep);
  }
  .edge-tab.left { left: -6px; top: 110px; }
  .edge-tab.right { right: -6px; top: 40px; }
  .front-brand {
    position: absolute; left: 36px; top: 118px;
  }
  .front-brand .name {
    font-weight: 700; font-size: 40px; letter-spacing: 2px; color: var(--ink); line-height: 1;
  }
  .front-brand .tagline {
    margin-top: 8px; font-size: 11px; font-weight: 700; letter-spacing: 3px; color: var(--ink);
  }
  .contact {
    position: absolute; left: 300px; top: 44px; width: 210px;
    padding-left: 16px; border-left: 1px solid #e3e6ec;
  }
  .contact .person { font-weight: 700; font-size: 21px; letter-spacing: .5px; color: var(--ink); }
  .contact .creds { font-size: 11.5px; color: var(--blue); margin: 3px 0 12px; }
  .contact ul { list-style: none; }
  .contact li {
    display: flex; align-items: center; gap: 8px;
    font-size: 13.5px; line-height: 21px; color: var(--ink);
  }
  .contact li svg { width: 12px; height: 12px; flex: none; }
  .contact .accent { color: var(--blue); }
  .plain-mark { width: 11px; height: 11px; border-radius: 50%; border: 1.6px solid var(--ink); flex: none; }
  .offer {
    position: absolute; bottom: 26px; left: 0; right: 0;
    display: flex; align-items: center; justify-content: center; gap: 12px;
    font-size: 15px; color: var(--ink);
  }
  .offer .rule { width: 44px; height: 2px; background: var(--blue); }
  .offer .free { color: var(--blue); }
</style>
</head>
<body>
<main class="stage">
  <section class="card card-back">
    <div class="back-brand">
      <span class="dot"></span>
      <span class="name">VANTRELO</span>
    </div>
    <p class="services">
      Personal Training<span class="sep"></span>Nutrition Coaching<span class="sep"></span>Golf Fitness<br>
      Injury Rehabilitation<span class="sep"></span>Massage Therapy<span class="sep"></span>Yoga
    </p>
  </section>

  <section class="card card-front">
    <span class="edge-tab left"></span>
    <span class="edge-tab right"></span>

    <div class="front-brand">
      <div class="name">VANTRELO</div>
      <div class="tagline">NUTRITION - FITNESS - HEALTH</div>
    </div>

    <div class="contact">
      <div class="person">DEREK FULHAM</div>
      <div class="creds">MSc, CAT(C), RMT, CSCS, Pn2</div>
      <ul>
        <li>
          <svg viewBox="0 0 12 12"><circle cx="6" cy="6" r="5.2" fill="none" stroke="#1f2533" stroke-width="1.2"/><path d="M4 3.5l1 1-.6.8a4 4 0 0 0 2.3 2.3l.8-.6 1 1-.8.8C5.8 8.6 3.4 6.2 3.2 4.3z" fill="#1f2533"/></svg>
          250-555-0147
        </li>
        <li>
          <svg viewBox="0 0 12 12"><rect x="1" y="2.5" width="10" height="7" fill="none" stroke="#1f2533" stroke-width="1.2"/><path d="M1 2.8l5 3.8 5-3.8" fill="none" stroke="#1f2533" stroke-width="1.2"/></svg>
          derek@vantrelo.com
        </li>
        <li>
          <svg viewBox="0 0 12 12"><circle cx="6" cy="6" r="5" fill="none" stroke="#1f2533" stroke-width="1.2"/><ellipse cx="6" cy="6" rx="2.2" ry="5" fill="none" stroke="#1f2533" stroke-width="1"/><path d="M1 6h10" stroke="#1f2533" stroke-width="1"/></svg>
          <span>www.<span class="accent">vantrelo</span>.com</span>
        </li>
        <li>
          <span class="plain-mark"></span>
          @derek_fulham
        </li>
      </ul>
    </div>

    <p class="offer">
      <span class="rule"></span>
      <span>Contact us to receive a <span class="free">FREE</span> assessment</span>
      <span class="rule"></span>
    </p>
  </section>
</main>
</body>
</html>
```